K7 Electrical Services Ltd Web design

I require a web site for my new electrical contracting company. We are customer service orientated. Offering high value electrical installations, design and maintenance. Focused on custom residential and commercial upgrading. Lighting design and application are paramount in our company's services. Industry leading product use and integration are always on the forefront with our customer client services. As well as energy efficiency.

Target Market(s)

Homebuilders, General Contractors, Property management companies, clients, individuals,

Industry/Entity Type

Electric Company

Coding

Coded - Design and coding required

Number of Pages Required

3 page

Requirements
Must have
• Classic, modern, edgy but not trendy . Appeals to the masse.
• 3 page
• home page
• about page
• gallery page
• ability to contact from the webiste
Nice to have
• open to all types of designs that are relative to the construction industry.
• Black, Grey, metallic ice blue and deep purple colours from the logo.
Should not have
• anything cheesy with cartoon light bulb images.

```html
<!DOCTYPE html>
<html lang="en">
<head>
<meta charset="utf-8">
<title>K7 Electrical Services Ltd</title>
<link href="https://fonts.googleapis.com/css2?family=Orbitron:wght@500;700&family=Raleway:wght@400;500;600;700&display=swap" rel="stylesheet">
<style>
:root{
  --purple:#5d2c91;
  --purple-deep:#4a1f78;
  --purple-light:#7b46b5;
  --ink:#222;
  --text:#555;
  --muted:#888;
  --line:#e3e3e3;
  --light:#f2f2f2;
  --footer:#141414;
  --white:#fff;
  --star:#f0b429;
}
*{box-sizing:border-box;margin:0;padding:0}
html,body{width:1200px;height:3475px;overflow:hidden}
body{position:relative;font-family:"Raleway",Arial,sans-serif;color:var(--text);background:var(--white)}
.abs{position:absolute}
.heading{font-family:"Orbitron",Arial,sans-serif;font-weight:500;color:var(--ink);text-align:center;letter-spacing:1px;text-transform:uppercase}
.divider{position:absolute;left:0;width:1200px;display:flex;justify-content:center;align-items:center;gap:12px;font-family:"Orbitron",sans-serif;font-size:11px;font-weight:700;color:var(--purple)}
.divider::before,.divider::after{content:"";width:80px;height:2px;background:var(--purple)}
.divider.light{color:#fff}.divider.light::before,.divider.light::after{background:#fff}

/* top bar */
.topbar{top:0;left:0;width:1200px;height:40px;background:var(--purple);color:#fff;font-size:13px;font-weight:600;display:flex;justify-content:flex-end;align-items:center;padding-right:40px;gap:14px}
.topbar .dots{display:flex;gap:7px}
.topbar .dots span{width:10px;height:10px;background:#fff;border-radius:2px}
/* header */
.header{top:40px;left:0;width:1200px;height:110px;background:#fff}
.logo{position:absolute;font-family:"Raleway",sans-serif;font-weight:700;color:var(--purple);text-align:center;line-height:1.05}
.header .logo{left:97px;top:24px;width:182px;font-size:24px}
.nav{position:absolute;top:0;left:396px;height:110px;font-size:15px;color:#333;font-weight:500}
.nav a{position:absolute;white-space:nowrap;color:inherit;text-decoration:none}
.nav a.active{color:var(--purple)}
.nav a.active::after{content:"";position:absolute;left:-6px;right:-6px;top:50px;height:3px;background:var(--purple)}
/* hero */
.hero{top:150px;left:0;width:1200px;height:492px;background:linear-gradient(180deg,#1a2a4c 0%,#304a72 40%,#6a5a46 72%,#2b2a1c 100%)}
.hero-box{position:absolute;left:271px;top:133px;width:658px;height:222px;background:rgba(255,255,255,.18);text-align:center;color:#fff}
.hero-box h1{font-family:"Orbitron",sans-serif;font-weight:700;font-size:50px;letter-spacing:2px;margin-top:22px}
.hero-box p{font-size:22px;margin-top:8px}
.btn{display:inline-flex;align-items:center;justify-content:center;border-radius:30px;font-weight:700;text-transform:uppercase}
.hero-box .btn{margin-top:22px;width:160px;height:40px;background:var(--purple);border:2px solid #fff;font-size:15px}
.arrow{position:absolute}
.notch{left:548px;top:618px}
/* about */
.about-text{left:210px;top:817px;width:782px;font-size:14px;line-height:1.9;color:var(--muted);text-align:center}
.tile{position:absolute;top:897px;width:431px;height:283px}
.tile span{position:absolute;bottom:22px;left:0;width:100%;text-align:center;color:#fff;font-weight:700;font-size:16px;text-transform:uppercase}
/* support band */
.support{top:1272px;left:0;width:1200px;height:146px;background:linear-gradient(90deg,#bdbdbd,#d6d6d6 60%,#c2c2c2)}
.support h3{position:absolute;left:157px;top:38px;color:#fff;font-size:27px;font-weight:700;text-transform:uppercase}
.support p{position:absolute;left:157px;top:82px;color:#fff;font-size:14px}
.support .btn{position:absolute;left:799px;top:51px;width:244px;height:44px;background:#fff;color:var(--purple);font-size:17px;gap:12px}
/* services */
.card{position:absolute;top:1610px;width:311px;height:114px;border:1px solid var(--line);background:#fff;padding:14px 16px 0 76px}
.card.active{border-right:4px solid var(--purple)}
.card h4{font-size:14px;font-weight:700;color:#333;text-transform:uppercase;line-height:1.2}
.card p{font-size:11.5px;line-height:1.45;color:var(--muted);margin-top:5px}
.card .more{font-size:11.5px;color:var(--purple);font-weight:600;margin-top:3px}
.card .icon{position:absolute;left:-21px;top:50px;width:78px;height:64px;display:flex;align-items:center;justify-content:center;background:#fff}
.card.active .icon{background:var(--purple)}
/* testimonials */
.clients{top:1875px;left:0;width:1200px;height:442px;background:linear-gradient(120deg,#3e1868 0%,#5d2c91 45%,#6f3aa8 70%,#4a1f78 100%)}
.clients .heading{color:#fff}
.quote{position:absolute;top:190px;width:320px;color:#fff}
.avatar{position:absolute;left:0;top:0;width:74px;height:74px;border-radius:50%;border:4px solid #fff;background:linear-gradient(160deg,#d8c6b8,#8a7a70)}
.quote .body{position:absolute;left:96px;top:8px;width:215px;font-size:13px;line-height:1.6}
.quote .name{position:absolute;left:96px;top:108px;font-size:10px;font-weight:700;text-transform:uppercase}
.quote .role{position:absolute;left:96px;top:124px;font-size:9.5px;white-space:nowrap}
.quote .stars{position:absolute;left:96px;top:160px;color:var(--star);font-size:20px;letter-spacing:3px}
.round-btn{position:absolute;width:36px;height:36px;border-radius:50%;border:1px solid #fff;display:flex;align-items:center;justify-content:center}
/* why */
.why{position:absolute;width:340px}
.why.left{left:91px;text-align:right}
.why.right{left:772px}
.why h4{font-size:15px;font-weight:700;color:#333;text-transform:uppercase}
.why p{font-size:13px;line-height:1.65;color:var(--muted);margin-top:10px}
.why .more{font-size:12px;color:var(--purple);font-weight:600;margin-top:8px}
.why-photo{left:450px;top:2521px;width:298px;height:298px;border-radius:50%;border:5px solid #ddd;background:radial-gradient(circle at 50% 65%,#e8a250 0%,#7a4a2a 30%,#1f2b4e 62%,#0e1a38 100%)}
/* partners */
.partners{top:2915px;left:0;width:1200px;height:132px;background:var(--light)}
.partner{position:absolute;top:30px;width:152px;height:72px;background:#fff;border:1px solid var(--line);display:flex;align-items:center;justify-content:center;font-weight:700;font-size:20px;color:#333;text-transform:uppercase}
/* footer */
.footer{top:3047px;left:0;width:1200px;height:428px;background:var(--footer);color:#fff}
.footer h5{position:absolute;top:95px;font-size:20px;font-weight:600}
.field{position:absolute;background:#fff;color:#999;font-size:14px;padding:10px 12px}
.submit{position:absolute;left:348px;top:232px;width:238px;height:39px;background:var(--purple);color:#fff;font-weight:700;font-size:15px;display:flex;align-items:center;justify-content:center}
.info{position:absolute;left:626px;display:flex;align-items:center;gap:18px;font-size:14px;line-height:1.6}
.info .ic{width:38px;height:38px;border-radius:50%;background:#2c2c2c;display:flex;align-items:center;justify-content:center;flex:none}
.footer .logo{left:892px;top:120px;width:210px;font-size:26px;color:#fff}
.social{position:absolute;left:900px;top:228px;display:flex;gap:9px}
.social span{width:30px;height:30px;border-radius:50%}
.footer .rule{position:absolute;left:97px;top:350px;width:1006px;height:1px;background:#333}
.copy{position:absolute;top:384px;left:0;width:1200px;text-align:center;font-size:12px;color:#ccc}
</style>
</head>
<body>

<div class="abs topbar">
  <span>&#9742; Call us : 1 800 555 0142</span><span>|</span><span>&#9993; Email us : info@k7electrical.com</span><span>|</span>
  <span class="dots"><span></span><span></span><span></span><span></span><span></span></span>
</div>

<header class="abs header">
  <div class="logo">K7<br>ELECTRICAL<br><small style="font-size:11px;letter-spacing:4px">SERVICES</small></div>
  <nav class="nav">
    <a class="active" style="left:0;top:42px">Home</a>
    <a style="left:77px;top:42px">About us</a>
    <a style="left:199px;top:42px">Services</a>
    <a style="left:317px;top:42px">Blog</a>
    <a style="left:405px;top:42px">Testimonials</a>
    <a style="left:554px;top:42px">Contact us</a>
    <svg class="arrow" style="left:689px;top:45px" width="16" height="16" viewBox="0 0 16 16"><circle cx="6.5" cy="6.5" r="5" fill="none" stroke="#5d2c91" stroke-width="2"/><line x1="10" y1="10" x2="15" y2="15" stroke="#5d2c91" stroke-width="2"/></svg>
  </nav>
</header>

<section class="abs hero" role="img" aria-label="Modern house at dusk with glowing interior lights">
  <svg class="arrow" style="left:56px;top:214px" width="30" height="70" viewBox="0 0 30 70"><polyline points="28,2 2,35 28,68" fill="none" stroke="#fff" stroke-width="2"/></svg>
  <svg class="arrow" style="left:1114px;top:214px" width="30" height="70" viewBox="0 0 30 70"><polyline points="2,2 28,35 2,68" fill="none" stroke="#fff" stroke-width="2"/></svg>
  <div class="hero-box">
    <h1>K7 ELECTRICAL</h1>
    <p>We are a new electrical contracting company</p>
    <span class="btn">Read More</span>
  </div>
</section>
<svg class="abs notch" width="104" height="32" viewBox="0 0 104 32"><path d="M0 24 Q52 -8 104 24 L104 32 L0 32Z" fill="#fff"/><polyline points="44,14 52,21 60,14" fill="none" stroke="#555" stroke-width="2"/></svg>

<h2 class="abs heading" style="left:0;top:726px;width:1200px;font-size:30px">About K7 Electrical</h2>
<div class="divider" style="top:780px">K7</div>
<p class="abs about-text">Sed ut perspiciatis unde omnis iste natus error sit voluptatem accusantium doloremque laudantium rem aperiam, eaque ipsa quae ab illo inventore veritatis et quasi architecto beatae voluptatem quia voluptas sit aspernatur</p>
<div class="tile" style="left:157px;background:linear-gradient(135deg,#6b4a2e,#c89a6a 55%,#8a6a4a)" role="img" aria-label="Electrician stripping a cable by hand"><span>Custom Residential</span></div>
<div class="tile" style="left:612px;background:linear-gradient(135deg,#4a4a48,#8a847a 50%,#b8b6b0)" role="img" aria-label="Electrician working at a commercial panel"><span>Commercial Upgrading</span></div>

<section class="abs support">
  <h3>Online Support 24H/7 For You</h3>
  <p>Lorem ipsum dolor sit amet, consectetur adipiscing elit ut text will appear here soon.</p>
  <span class="btn">Call Us Here <span>&#187;</span></span>
</section>

<h2 class="abs heading" style="left:0;top:1498px;width:1200px;font-size:30px">Our Services</h2>
<div class="divider" style="top:1552px">K7</div>
<div class="card active" style="left:109px">
  <div class="icon"><svg width="40" height="40" viewBox="0 0 40 40"><path d="M6 34 L22 18 M18 10 a8 8 0 0 0 12 12 l-4 -4 l2 -4 l4 -2 l4 4 a8 8 0 0 0 -12 -12Z M30 34 L8 12 L5 5 L12 8 Z" fill="none" stroke="#fff" stroke-width="3"/></svg></div>
  <h4>Electrical Installations</h4>
  <p>Sed ut perspiciatis unde omnis iste natus error sit voluptatem accusantium doloremque laudantium.</p>
  <div class="more">Read More &#187;</div>
</div>
<div class="card" style="left:454px">
  <div class="icon"><svg width="40" height="40" viewBox="0 0 40 40"><path d="M8 32 L16 24 M14 14 L26 26 L30 22 L18 10 Z M22 14 L28 8 M26 18 L32 12" fill="none" stroke="#5d2c91" stroke-width="3"/></svg></div>
  <h4>Design</h4>
  <p>Sed ut perspiciatis unde omnis iste natus error sit voluptatem accusantium doloremque laudantium.</p>
  <div class="more">Read More &#187;</div>
</div>
<div class="card" style="left:799px">
  <div class="icon"><svg width="40" height="40" viewBox="0 0 40 40"><rect x="10" y="20" width="20" height="16" rx="3" fill="#5d2c91"/><circle cx="20" cy="12" r="7" fill="none" stroke="#5d2c91" stroke-width="3"/><path d="M8 14 L14 8" stroke="#5d2c91" stroke-width="3"/></svg></div>
  <h4>Maintenance</h4>
  <p>Sed ut perspiciatis unde omnis iste natus error sit voluptatem accusantium doloremque laudantium.</p>
  <div class="more">Read More &#187;</div>
</div>

<section class="abs clients">
  <h2 class="abs heading" style="left:0;top:70px;width:1200px;font-size:30px">What Clients Say</h2>
  <div class="divider light" style="top:124px">K7</div>
  <div class="round-btn" style="left:28px;top:257px"><svg width="10" height="12" viewBox="0 0 10 12"><path d="M8 0 L0 6 L8 12Z" fill="#fff"/></svg></div>
  <div class="round-btn" style="left:1134px;top:257px"><svg width="10" height="12" viewBox="0 0 10 12"><path d="M2 0 L10 6 L2 12Z" fill="#fff"/></svg></div>
  <div class="quote" style="left:97px">
    <div class="avatar" role="img" aria-label="Client portrait"></div>
    <p class="body">&#8220; At vero eos et accusamus et iusto odio dignissimos ducimus qui blanditiis praesentium voluptatum.</p>
    <div class="name">Marla Jensen</div><div class="role">Financial Services Professional</div>
    <div class="stars">&#9733;&#9733;&#9733;&#9733;&#9734;</div>
  </div>
  <div class="quote" style="left:445px">
    <div class="avatar" role="img" aria-label="Client portrait"></div>
    <p class="body">&#8220; At vero eos et accusamus et iusto odio dignissimos ducimus qui blanditiis praesentium voluptatum.</p>
    <div class="name">Tobias R. Lindqvist</div><div class="role">National Urban Fellow at the Harbour</div>
    <div class="stars">&#9733;&#9733;&#9733;&#9733;&#9734;</div>
  </div>
  <div class="quote" style="left:792px">
    <div class="avatar" role="img" aria-label="Client portrait"></div>
    <p class="body">&#8220; At vero eos et accusamus et iusto odio dignissimos ducimus qui blanditiis praesentium voluptatum.</p>
    <div class="name">Rhea Calloway</div><div class="role">Creative Strategist | Entrepreneur &amp; Founder</div>
    <div class="stars">&#9733;&#9733;&#9733;&#9733;&#9734;</div>
  </div>
</section>

<h2 class="abs heading" style="left:0;top:2397px;width:1200px;font-size:30px">Why Choose Us</h2>
<div class="divider" style="top:2451px">K7</div>
<div class="why left" style="top:2522px"><h4>Private Security</h4><p>Sed ut perspiciatis unde omnis iste natus error sit voluptatem accusantium doloremque laudantium, totam rem aperiam, eaque ipsa quae.</p><div class="more">Read More &#187;</div></div>
<div class="why left" style="top:2693px"><h4>Best Materials</h4><p>Sed ut perspiciatis unde omnis iste natus error sit voluptatem accusantium doloremque laudantium, totam rem aperiam, eaque ipsa quae.</p><div class="more">Read More &#187;</div></div>
<div class="why right" style="top:2522px"><h4>Data Protection</h4><p>Sed ut perspiciatis unde omnis iste natus error sit voluptatem accusantium doloremque laudantium, totam rem aperiam, eaque ipsa quae.</p><div class="more">Read More &#187;</div></div>
<div class="why right" style="top:2693px"><h4>Professional Workers</h4><p>Sed ut perspiciatis unde omnis iste natus error sit voluptatem accusantium doloremque laudantium, totam rem aperiam, eaque ipsa quae.</p><div class="more">Read More &#187;</div></div>
<div class="abs why-photo" role="img" aria-label="Lit family home at night"></div>

<section class="abs partners">
  <svg class="arrow" style="left:96px;top:56px" width="12" height="20" viewBox="0 0 12 20"><polyline points="10,2 2,10 10,18" fill="none" stroke="#333" stroke-width="2"/></svg>
  <div class="partner" style="left:134px">Northgate</div>
  <div class="partner" style="left:297px">Ridgeline</div>
  <div class="partner" style="left:457px">Voltmark</div>
  <div class="partner" style="left:617px">Brightway</div>
  <div class="partner" style="left:776px">Ironworks</div>
  <div class="partner" style="left:927px">Keystone</div>
  <svg class="arrow" style="left:1092px;top:56px" width="12" height="20" viewBox="0 0 12 20"><polyline points="2,2 10,10 2,18" fill="none" stroke="#333" stroke-width="2"/></svg>
</section>

<footer class="abs footer">
  <svg class="abs" style="left:0;top:-1px" width="1200" height="14" viewBox="0 0 1200 14"><path d="M0 0 H1200 L1200 0 Q1100 12 1000 0Z M200 0 Q100 12 0 0Z" fill="#f2f2f2"/></svg>
  <h5 style="left:97px">Get in Touch</h5>
  <div class="field" style="left:97px;top:132px;width:241px;height:39px">Name</div>
  <div class="field" style="left:97px;top:185px;width:241px;height:39px">Email</div>
  <div class="field" style="left:97px;top:232px;width:241px;height:39px">Phone</div>
  <div class="field" style="left:348px;top:132px;width:238px;height:88px">Message</div>
  <div class="submit">SUBMIT MESSAGE</div>
  <h5 style="left:626px">Contact Info</h5>
  <div class="info" style="top:130px;width:240px"><span class="ic"><svg width="16" height="16" viewBox="0 0 16 16"><path d="M8 1 L15 8 H13 V15 H3 V8 H1Z" fill="#fff"/></svg></span><span>124,Lk enim ad minima veni amquis nostrum</span></div>
  <div class="info" style="top:189px"><span class="ic"><svg width="16" height="16" viewBox="0 0 16 16"><path d="M3 1 L6 1 L7 5 L5 6.5 Q7 10 9.5 11 L11 9 L15 10 L15 13 Q14 15 12 15 Q2 13 1 3 Q1 1 3 1Z" fill="#fff"/></svg></span><span>Phone : 1 800 555 0142</span></div>
  <div class="info" style="top:247px"><span class="ic"><svg width="16" height="12" viewBox="0 0 16 12"><rect x="0.5" y="0.5" width="15" height="11" fill="none" stroke="#fff"/><polyline points="0.5,0.5 8,7 15.5,0.5" fill="none" stroke="#fff"/></svg></span><span>info@k7electrical.com</span></div>
  <div class="logo">K7<br>ELECTRICAL<br><small style="font-size:12px;letter-spacing:5px">SERVICES</small></div>
  <div class="social"><span style="background:#3b5998"></span><span style="background:#1da1f2"></span><span style="background:#d62d20"></span><span style="background:#0077b5"></span><span style="background:#dd4b39"></span></div>
  <div class="rule"></div>
  <p class="copy">&#169; Copyright 2018 K7 Electrical.All Rights Reserved &nbsp;|&nbsp; Privacy policy &nbsp;|&nbsp; Terms and use</p>
</footer>

</body>
</html>
```